Our new beauty salon requires a price list brochure

Our beauty clinic is a medical grade skin care clinic. So our salon is very clinical and professional in appearance. I would like the colours to be similar to our logo design with some nice texture or abstract shapes thrown in.
Pricelist, contact details and logo is attached
I would prefer it to be a 3 fold brochure.

Target Market(s)

Females aged 30-50

Colors
85acd3
cedeed
c4c4c4
5c5c5c
000000
ffffff
eea3c7
f9d9e8
dbdbdb

Requirements
Must have
• easy to read

```html
<!DOCTYPE html>
<html lang="en">
<head>
<meta charset="utf-8">
<title>Ivel Aesthetics – Price List Brochure</title>
<link href="https://fonts.googleapis.com/css2?family=Arimo:wght@400;700&display=swap" rel="stylesheet">
<style>
  :root{
    --blue:#85acd3;
    --blue-pale:#cedeed;
    --grey-light:#c4c4c4;
    --grey-bg:#b9b9b9;
    --grey-mid:#5c5c5c;
    --grey-dark:#474747;
    --slate:#4d5b68;
    --ink:#222;
    --white:#ffffff;
  }
  *{box-sizing:border-box;margin:0;padding:0}
  html,body{width:1200px;height:1200px;overflow:hidden}
  body{background:var(--grey-bg);font-family:"Arimo",Arial,sans-serif;position:relative}

  .sheet{position:absolute;left:221px;width:773px;height:546px;overflow:hidden}
  .sheet--outside{top:36px;background:var(--white)}
  .sheet--inside{top:617px;display:flex}

  /* outside */
  .feature-panel{position:absolute;left:0;top:0;width:258px;height:440px;
    background:radial-gradient(circle at 30% 40%,#9bbde0,var(--blue) 70%);}
  .hero-photo{position:absolute;left:258px;top:0;width:515px;height:480px;
    background:radial-gradient(ellipse at 65% 45%,#e9b98f 0%,#b87436 35%,#5a3318 70%,#2d1a0d 100%);}
  .corner-mark{position:absolute;left:691px;top:18px;width:70px;height:48px;background:var(--slate);
    color:var(--white);font-size:13px;display:flex;align-items:center;justify-content:center;letter-spacing:1px}
  .wave{position:absolute;left:0;top:0;width:773px;height:546px}

  .treatment{position:absolute;left:13px;width:240px;color:#555}
  .treatment h3{font-size:13px;font-weight:700;line-height:15px}
  .treatment p{font-size:9px;line-height:11px;color:var(--white);margin-top:8px}

  .brand{position:absolute;left:24px;top:440px;color:var(--slate);text-align:center;width:212px}
  .brand__name{font-size:58px;line-height:60px;letter-spacing:4px}
  .brand__sub{font-size:9px;letter-spacing:9px;margin-top:6px}

  .social{position:absolute;left:315px;font-size:9px;color:var(--ink);display:flex;align-items:center;gap:8px}
  .social__icon{width:9px;height:9px;background:var(--blue)}
  .website{position:absolute;left:315px;top:512px;font-size:11px;color:var(--ink)}
  .address{position:absolute;right:9px;top:473px;font-size:9px;line-height:9.2px;text-align:right;color:var(--ink)}
  .address .phone{margin-top:4px;margin-right:4px}

  /* inside */
  .column{position:relative;width:258px;height:546px;
    background:repeating-linear-gradient(45deg,rgba(255,255,255,.03) 0 2px,transparent 2px 5px),var(--grey-mid)}
  .column--middle{background:repeating-linear-gradient(45deg,rgba(255,255,255,.03) 0 2px,transparent 2px 5px),var(--grey-dark)}
  .column--right{width:257px}
  .section-title{position:absolute;left:13px;font-size:21px;line-height:24px;font-weight:700;color:var(--blue)}
  .price-list{position:absolute;left:13px;right:14px;list-style:none;font-size:10.5px;line-height:12.1px;color:var(--white)}
  .price-list li{display:flex;justify-content:space-between}
  .price-list li.gap{height:12.1px}
  .price-list--small{font-size:9px;line-height:11.2px;right:16px}

  .menu-row{position:absolute;left:13px;right:16px;display:flex;align-items:baseline;color:var(--white)}
  .menu-row__name{font-size:14px;font-weight:700;color:var(--blue)}
  .menu-row__note{font-size:9px;color:#111;margin-left:5px}
  .menu-row__price{font-size:9px;margin-left:auto}
  .note{font-size:9px;color:#111;font-weight:400}
</style>
</head>
<body>

<section class="sheet sheet--outside" aria-label="Brochure outside">
  <div class="feature-panel"></div>
  <div class="hero-photo" role="img" aria-label="Portrait photograph of a woman with evening makeup in front of warm golden sparkling lights"></div>
  <div class="corner-mark">ivel</div>

  <svg class="wave" viewBox="0 0 773 546" aria-hidden="true">
    <path d="M0 434 C110 375 260 350 420 385 C560 415 620 470 773 420" fill="none" stroke="#5c5c5c" stroke-width="9"/>
    <path d="M0 438 C110 379 260 354 420 389 C560 419 620 474 773 424 L773 546 L0 546 Z" fill="#ffffff"/>
  </svg>

  <div class="treatment" style="top:57px">
    <h3>Lumavex LED</h3>
    <p>$90 per treatment &nbsp; or<br>$50 when added on to any of our other skin treatments</p>
  </div>
  <div class="treatment" style="top:127px">
    <h3>Microvex Microneedling (Collagen In-<br>duction Therapy)</h3>
    <p>$350 full face<br>$450 face, neck and décolletage</p>
  </div>
  <div class="treatment" style="top:218px">
    <h3>Novara Laser Facial</h3>
    <p>$350 full face<br>$450 face, neck and décolletage</p>
  </div>

  <div class="brand">
    <div class="brand__name">ivel</div>
    <div class="brand__sub">AESTHETICS</div>
  </div>

  <div class="social" style="top:468px"><span class="social__icon"></span>ivel_aesthetics</div>
  <div class="social" style="top:490px"><span class="social__icon"></span>ivel aesthetics australia</div>
  <div class="website">www.ivelaesthetics.com.au</div>

  <address class="address" style="font-style:normal">
    Ivel Aesthetics<br>4/27 Harbour Road<br>Westbrook<br>Western Australia
    <div class="phone">(08) 5550 1234</div>
  </address>
</section>

<section class="sheet sheet--inside" aria-label="Brochure inside price list">
  <div class="column column--left">
    <h2 class="section-title" style="top:32px">IPL Hair Removal</h2>
    <ul class="price-list" style="top:66px">
      <li><span>Upper lip</span><span>$50</span></li>
      <li><span>Chin</span><span>$50</span></li>
      <li><span>Cheeks</span><span>$75</span></li>
      <li><span>Whole face</span><span>$350</span></li>
      <li class="gap"></li>
      <li><span>Bikini</span><span>$90</span></li>
      <li><span>G String</span><span>$120</span></li>
      <li><span>Brazilian</span><span>$150</span></li>
      <li class="gap"></li>
      <li><span>Underarms</span><span>$90</span></li>
      <li><span>Half arm</span><span>$180</span></li>
      <li><span>Full arm</span><span>$250</span></li>
      <li><span>Half leg</span><span>$290</span></li>
      <li><span>Thighs</span><span>$290</span></li>
      <li><span>Full leg</span><span>$490</span></li>
      <li class="gap"></li>
      <li><span>Full back</span><span>$350</span></li>
      <li><span>Shoulders</span><span>$180</span></li>
      <li><span>Nipples</span><span>$60</span></li>
      <li><span>Snail trail</span><span>$50</span></li>
      <li><span>Stomach</span><span>$250</span></li>
      <li><span>Chest</span><span>$250</span></li>
      <li><span>Buttocks</span><span>$200</span></li>
    </ul>
    <h2 class="section-title" style="top:370px">IPL Photo Rejuvenation</h2>
    <ul class="price-list" style="top:404px">
      <li><span>Full face</span><span>$350</span></li>
      <li><span>Neck</span><span>$200</span></li>
      <li><span>Face, neck ad décolletage</span><span>$450</span></li>
      <li><span>Spot Treatment</span><span>$50</span></li>
    </ul>
  </div>

  <div class="column column--middle">
    <h2 class="section-title" style="top:32px">Waxing</h2>
    <ul class="price-list" style="top:66px">
      <li><span>Eyebrow</span><span>$21</span></li>
      <li><span>Lip</span><span>$15</span></li>
      <li><span>Chin</span><span>$15</span></li>
      <li><span>Sides of face</span><span>$20</span></li>
      <li><span>Underarm</span><span>$20</span></li>
      <li><span>Forearm</span><span>$25</span></li>
      <li><span>Full arm</span><span>$35</span></li>
      <li><span>Lower leg</span><span>$30</span></li>
      <li><span>Upper leg</span><span>$30</span></li>
      <li><span>Full leg</span><span>$50</span></li>
      <li><span>Inner thigh</span><span>$10</span></li>
      <li><span>Snail trail</span><span>$10</span></li>
      <li><span>Bikini</span><span>$30</span></li>
      <li><span>G String</span><span>$40</span></li>
      <li><span>Brazilian</span><span>$50</span></li>
      <li class="gap"></li>
      <li><span>Eyebrow wax and Lip wax</span><span>$30</span></li>
      <li><span>Eyebrow, lip and chin wax</span><span>$45</span></li>
    </ul>
    <h2 class="section-title" style="top:306px">Mens waxing</h2>
    <ul class="price-list" style="top:340px">
      <li><span>Mono brow</span><span>$5</span></li>
      <li><span>Eyebrow</span><span>$21</span></li>
      <li><span>Neck</span><span>$20</span></li>
      <li><span>Full back</span><span>$45</span></li>
      <li><span>Chest and Abdomen</span><span>$45</span></li>
    </ul>
    <h2 class="section-title" style="top:420px">Tinting</h2>
    <ul class="price-list" style="top:453px">
      <li><span>Eyelash Tint</span><span>$25</span></li>
      <li><span>Lash Lift and Tint</span><span>$80</span></li>
      <li class="gap"></li>
      <li><span>Henna eyebrows and wax</span><span>$80</span></li>
      <li><span>Eyelash Tint and brow wax</span><span>$40</span></li>
    </ul>
  </div>

  <div class="column column--right">
    <div class="menu-row" style="top:37px"><span class="menu-row__name">Ivel Mini Facial</span><span class="menu-row__note">(40min)</span><span class="menu-row__price">$80</span></div>
    <div class="menu-row" style="top:64px"><span class="menu-row__name">Ivel Deluxe Facial</span><span class="menu-row__note">(1 hour)</span><span class="menu-row__price">$110</span></div>
    <div class="menu-row" style="top:90px"><span class="menu-row__name">Microdermabrasion</span><span class="menu-row__price">$125</span></div>
    <div class="menu-row" style="top:117px"><span class="menu-row__name">Mini Micro</span><span class="menu-row__price">$80</span></div>

    <h2 class="section-title" style="top:154px">Wrinkle Relaxers</h2>
    <ul class="price-list price-list--small" style="top:185px">
      <li><span>per area (Crows, frown lines, forehead lines)</span><span>$175</span></li>
      <li><span>or all 3 areas for</span><span>$450</span></li>
      <li><span>minor areas (Gummy smile, brow lift, bunny lines)</span><span>$50</span></li>
    </ul>

    <h2 class="section-title" style="top:234px">Dermal Fillers and<br>Lip Fillers<span class="note">per ml</span></h2>
    <div class="menu-row" style="top:264px"><span class="menu-row__price">$500</span></div>

    <h2 class="section-title" style="top:298px">Chemical Peels<br>Aspira Skin Peels<span class="note">30min</span></h2>
    <ul class="price-list price-list--small" style="top:353px">
      <li><span>Lactic Acid Peels 20%/40%/60%</span><span>$120</span></li>
      <li><span>Age Defining Peel</span><span>$120</span></li>
      <li><span>Complete Pigment Peel</span><span>$120</span></li>
      <li><span>Problem Skin Peel</span><span>$120</span></li>
    </ul>

    <h2 class="section-title" style="top:415px">Cosmalune Peels <span class="note">30min</span></h2>
    <ul class="price-list price-list--small" style="top:447px">
      <li><span>Blueberry Peel</span><span>$120</span></li>
      <li><span>Pomegranate Peel</span><span>$120</span></li>
      <li><span>Benefit Peel</span><span>$120</span></li>
      <li><span>Timeless Retinol Peel</span><span>$250</span></li>
    </ul>
  </div>
</section>

</body>
</html>
```